Quillbrookes websites redesign

Www.quill-brookes.com needs to be redesigned along with updations. The incremental material will be provided for the updations. We are looking for complete redesign of the pages with the new content. The complete write up will be provided soon

Target Market(s)

Global

Coding

Coded - Design and coding required

Number of Pages Required

5+ page

Requirements
Must have
• A clean and slick design for the Consulting.
Should not have
• Too many pictures which reduces the speed of the site

```html
<!DOCTYPE html>
<html lang="en">
<head>
<meta charset="utf-8">
<title>Quillbrookes – Contact</title>
<link href="https://fonts.googleapis.com/css2?family=Montserrat:wght@400;500;700&family=Arimo:wght@400;700&display=swap" rel="stylesheet">
<style>
:root{
  --accent:#39a8cf;
  --ink:#333;
  --muted:#8a8a8a;
  --line:#dcdcdc;
  --brand:#2b3550;
  --footer-bg:#161616;
  --footer-text:#a9a9a9;
  --footer-head:#ececec;
}
*{box-sizing:border-box;margin:0;padding:0}
html,body{width:1200px;height:1026px;overflow:hidden;background:#fff}
body{position:relative;font-family:"Arimo",Arial,sans-serif;color:var(--ink)}
.abs{position:absolute}

/* header */
.site-header{position:absolute;left:0;top:0;width:1200px;height:83px;border-bottom:1px solid #e6e6e6}
.brand{position:absolute;left:168px;top:24px;display:flex;align-items:center;gap:10px;font-family:"Arimo",Arial,sans-serif;font-size:29px;color:var(--brand);letter-spacing:.2px}
.brand-dot{width:36px;height:36px;border-radius:50%;background:var(--brand)}
.main-nav a{position:absolute;top:37px;font-size:13px;color:#666;text-decoration:none}
.main-nav a.active{color:var(--accent)}
.nav-underline{position:absolute;left:1006px;top:80px;width:42px;height:3px;background:var(--accent)}

/* intro */
.page-title{position:absolute;left:167px;top:149px;font-family:"Montserrat",sans-serif;font-weight:400;font-size:22px;color:#555;letter-spacing:.2px}
.page-title strong{font-weight:700}
.page-lead{position:absolute;left:167px;top:187px;font-size:11.2px;color:#444}

/* form */
.field{position:absolute;left:167px;width:400px;border:1px solid var(--line);font-size:12px;color:#999;padding:14px 18px}
.send-btn{position:absolute;left:167px;top:537px;width:400px;height:43px;background:var(--accent);color:#fff;font-family:"Montserrat",sans-serif;font-weight:500;font-size:12.5px;letter-spacing:1.6px;display:flex;align-items:center;justify-content:center}

/* contact details */
.info-label{position:absolute;left:643px;font-family:"Montserrat",sans-serif;font-size:11.5px;letter-spacing:1.6px;color:#8a8a8a}
.info-body{position:absolute;left:643px;font-size:12px;line-height:19.2px;color:#333}
.info-body b{font-weight:700;color:#444}

/* footer */
.site-footer{position:absolute;left:0;top:671px;width:1200px;height:355px;background:var(--footer-bg)}
.footer-brand{position:absolute;left:167px;top:62px;display:flex;align-items:center;gap:8px;font-size:22px;color:#8d8d8d}
.footer-brand .brand-dot{width:30px;height:30px;background:#8d8d8d}
.footer-text{position:absolute;font-size:11.5px;line-height:19.2px;color:var(--footer-text)}
.footer-head{position:absolute;font-family:"Montserrat",sans-serif;font-size:13.5px;color:var(--footer-head)}
.footer-rule{position:absolute;width:29px;height:1px;background:#bbb}
.accent-strong{color:var(--accent);font-weight:700;font-size:12.5px}
.accent-link{color:var(--accent);text-decoration:underline}
.subscribe{position:absolute;left:451px;top:146px;width:201px;height:36px;border:1px solid #888;padding:11px 14px;font-size:11.5px;color:#ddd}
.subscribe svg{position:absolute;right:9px;top:12px}
.site-links{position:absolute;left:736px;top:113px;list-style:none}
.site-links li{height:24px;font-size:11.5px;color:var(--footer-text);display:flex;align-items:center;gap:8px}
.site-links li span.ch{font-size:9px;color:#888}
.site-links li.active a{color:var(--accent)}
.social{position:absolute;left:922px;top:117px;display:flex;gap:4px}
.social span{width:28px;height:28px;border-radius:50%;border:2px solid #bbb}
.social span:first-child{border-color:var(--accent)}
.footer-bottom{position:absolute;left:0;top:300px;width:1200px;border-top:1px solid #333}
.copyright{position:absolute;left:168px;top:322px;font-size:11.5px;color:#999}
</style>
</head>
<body>

<header class="site-header">
  <div class="brand"><span class="brand-dot"></span>Quillbrookes</div>
  <nav class="main-nav">
    <a style="left:585px">home</a>
    <a style="left:656px">founder</a>
    <a style="left:731px">consultancy</a>
    <a style="left:831px">platform</a>
    <a style="left:903px">case studies</a>
    <a class="active" style="left:1005px">contact</a>
  </nav>
  <div class="nav-underline"></div>
</header>

<h1 class="page-title">QUILLBROOKE <strong>CONTACT US</strong></h1>
<p class="page-lead">Some of the deals completed by QCL are summarised below to describe the range of activities undertaken with Corporates</p>

<form class="contact-form">
  <div class="field" style="top:250px;height:43px">Name*</div>
  <div class="field" style="top:301px;height:43px">Email Address*</div>
  <div class="field" style="top:352px;height:43px">Phone</div>
  <div class="field" style="top:403px;height:108px">Message</div>
  <div class="send-btn">SEND MESSAGE</div>
</form>

<div class="info-label" style="top:244px">ADDRESS</div>
<div class="info-body" style="top:275px"><b>Quillbrookes Consultancy Ltd</b><br>Unit 04, 9th Floor, Harbourline Tower,<br>18 Larkspur Road, Kowloon<br>Hong Kong</div>

<div class="info-label" style="top:397px">TELEPHONES</div>
<div class="info-body" style="top:424px">+852-2555 0142 (landline)<br>+852-2555 0198 (fax)</div>

<div class="info-label" style="top:518px">EMAIL</div>
<div class="info-body" style="top:545px">query@quill-brookes.com<br>www.quill-brookes.com</div>

<footer class="site-footer">
  <div class="footer-brand"><span class="brand-dot"></span>Quillbrookes</div>
  <div class="footer-text" style="left:170px;top:113px">Quillbrookes Consultancy Ltd<br>Unit 04, 9th Floor, Harbourline Tower,<br>18 Larkspur Road, Kowloon<br>Hong Kong</div>
  <div class="footer-text" style="left:170px;top:209px">T: <span class="accent-strong">852-25550142</span><br>E: <span class="accent-link">query@quill-brookes.com</span></div>

  <div class="footer-head" style="left:452px;top:68px">GET IN TOUCH!</div>
  <div class="footer-rule" style="left:452px;top:97px"></div>
  <div class="footer-text" style="left:452px;top:113px">Simply Drop Your Mail Here</div>
  <div class="subscribe">Your Email Here
    <svg width="17" height="11" viewBox="0 0 17 11"><rect x=".5" y=".5" width="16" height="10" fill="none" stroke="#39a8cf"/><path d="M.5 .5 8.5 6.5 16.5 .5M.5 10.5 6 5M16.5 10.5 11 5" fill="none" stroke="#39a8cf"/></svg>
  </div>

  <div class="footer-head" style="left:735px;top:67px">SITE LINKS</div>
  <div class="footer-rule" style="left:736px;top:96px"></div>
  <ul class="site-links">
    <li class="active"><span class="ch">»</span><a class="accent-link">Home</a></li>
    <li><span class="ch">»</span>Founder</li>
    <li><span class="ch">»</span>Consultancy</li>
    <li><span class="ch">»</span>System</li>
    <li><span class="ch">»</span>Case Studies</li>
    <li><span class="ch">»</span>Contact</li>
  </ul>

  <div class="footer-head" style="left:920px;top:67px">SOCIAL LINKS</div>
  <div class="footer-rule" style="left:921px;top:96px"></div>
  <div class="social"><span></span><span></span><span></span><span></span></div>

  <div class="footer-bottom"></div>
  <div class="copyright">© Quillbrookes Consultancy Limited</div>
</footer>

</body>
</html>
```